Briefpapier und Visitenkarten für Bayerisches Gasthaus mit Zimmer
Zielgruppe
Traditionelle Gaststätte im Zentrum einer Kleinstadt in Bayern. Direkt am Marktplatz. 10 Gästezimmer.
Bayerisch. Traditionell. Von junger Geschäftsführerin geführt, mit jungem Personal. Wir haben das Objekt erst vor Kurzem erworben und fangen gerade an.
Gerichte: Braten, Steaks, Brotzeiten, vegetarische und VEGANE Speisen
Getränke: Sehr bierlastig. Es war früher ein Brauereigasthaus. Heute gibts auch eine kleine feine Weinkarte.
Zielgruppe sind Einheimische und Touristen. Im Sommer kommen Radfahrer und Wanderer. Besonders angesprochen werden auch Kinder. Es gibt eine großzügige Spielecke.
Aufgabenstellung
Das Gasthaus heißt Falke. Daher spielt der Falke im Design auch eine wichtige Rolle.
Nachdem wir sehr familienorientiert sind, könnte ich mir auch eine Falke-Familie vorstellen.
Visitenkarten und Briefpapier sollen alle wichtigen Infos enthalten, aber dabei sehr klar gehalten werden und nicht überladen sein. Mir ist ein schlichtes und ansprechendes Design wichtig. Es soll nicht verspielt sein.
Hier ist die Homepage:
www.falke-haldenau-gast.de
Info auf Briefpapier:
GASTHAUS FALKE
Trauber GmbH
Als Info auf Visitenkarte:
Gasthaus Falke

```html
<!DOCTYPE html>
<html lang="de">
<head>
<meta charset="utf-8">
<title>Gasthaus Falke – Visitenkarten</title>
<link rel="stylesheet" href="https://fonts.googleapis.com/css2?family=Exo+2:wght@300;400&display=swap">
<style>
  :root {
    --canvas: #dcdcdc;
    --dark-start: #0e0e0e;
    --dark-end: #373737;
    --green-start: #66882f;
    --green-end: #7ba43a;
    --green: #6f9a33;
    --green-deep: #5a8a1e;
    --white: #ffffff;
    --text-on-dark: #cfcfcf;
    --text-on-white: #b9b9b9;
  }
  * { box-sizing: border-box; margin: 0; padding: 0; }
  html, body { width: 1200px; height: 1200px; overflow: hidden; }
  body {
    background: var(--canvas);
    position: relative;
    font-family: "Exo 2", sans-serif;
    font-weight: 300;
  }
  .card {
    position: absolute;
    width: 546px;
    height: 308px;
    overflow: hidden;
  }
  .card--front { left: 24px; }
  .card--back  { left: 600px; }
  .row-1 { top: 10px; }
  .row-2 { top: 338px; }
  .row-3 { top: 677px; }

  .theme-dark  { background: linear-gradient(90deg, var(--dark-start), var(--dark-end)); }
  .theme-white { background: var(--white); box-shadow: 0 0 0 1px #d0d0d0; }
  .theme-green { background: linear-gradient(90deg, var(--green-start), var(--green-end)); }

  .brand {
    position: absolute;
    display: flex;
    align-items: center;
    gap: 12px;
    white-space: nowrap;
  }
  .brand-square { display: block; }
  .brand-name { font-weight: 400; }

  .card--front .brand {
    left: 50%;
    top: 50%;
    transform: translate(-50%, -50%);
  }
  .card--front .brand-square { width: 58px; height: 58px; }
  .card--front .brand-name { font-size: 30px; }

  .card--back .brand { left: 26px; bottom: 46px; gap: 8px; }
  .card--back .brand-square { width: 30px; height: 30px; }
  .card--back .brand-name { font-size: 15px; }

  .theme-dark .brand-square  { background: var(--green); }
  .theme-dark .brand-name    { color: var(--green); }
  .theme-white .brand-square { background: var(--green); }
  .theme-white .brand-name   { color: var(--green-deep); }
  .theme-green .brand-square { background: var(--white); }
  .theme-green .brand-name   { color: var(--white); }

  .contact {
    position: absolute;
    right: 26px;
    top: 130px;
    text-align: right;
    font-size: 12px;
    line-height: 14px;
  }
  .contact p + p { margin-top: 14px; }
  .contact .title { font-weight: 400; }
  .theme-dark .contact  { color: var(--text-on-dark); }
  .theme-dark .title    { color: var(--green); }
  .theme-white .contact { color: var(--text-on-white); }
  .theme-white .title   { color: var(--green-deep); }
  .theme-green .contact { color: var(--white); }
  .theme-green .title   { color: var(--white); }
</style>
</head>
<body>

  <section class="card card--front row-1 theme-dark">
    <div class="brand"><span class="brand-square"></span><span class="brand-name">Gasthaus Falke</span></div>
  </section>
  <section class="card card--back row-1 theme-dark">
    <div class="brand"><span class="brand-square"></span><span class="brand-name">Gasthaus Falke</span></div>
    <div class="contact">
      <p class="title">Gasthaus Falke<br>Haldenau im Lautertal</p>
      <p>Trauber GmbH<br>Kirchgasse 7<br>93412 Haldenau</p>
      <p>Tel. 09447 3815</p>
      <p>www.falke-haldenau-gast.de<br>info@falke-haldenau-gast.de</p>
    </div>
  </section>

  <section class="card card--front row-2 theme-white">
    <div class="brand"><span class="brand-square"></span><span class="brand-name">Gasthaus Falke</span></div>
  </section>
  <section class="card card--back row-2 theme-white">
    <div class="brand"><span class="brand-square"></span><span class="brand-name">Gasthaus Falke</span></div>
    <div class="contact">
      <p class="title">Gasthaus Falke<br>Haldenau im Lautertal</p>
      <p>Trauber GmbH<br>Kirchgasse 7<br>93412 Haldenau</p>
      <p>Tel. 09447 3815</p>
      <p>www.falke-haldenau-gast.de<br>info@falke-haldenau-gast.de</p>
    </div>
  </section>

  <section class="card card--front row-3 theme-green">
    <div class="brand"><span class="brand-square"></span><span class="brand-name">Gasthaus Falke</span></div>
  </section>
  <section class="card card--back row-3 theme-green">
    <div class="brand"><span class="brand-square"></span><span class="brand-name">Gasthaus Falke</span></div>
    <div class="contact">
      <p class="title">Gasthaus Falke<br>Haldenau im Lautertal</p>
      <p>Trauber GmbH<br>Kirchgasse 7<br>93412 Haldenau</p>
      <p>Tel. 09447 3815</p>
      <p>www.falke-haldenau-gast.de<br>info@falke-haldenau-gast.de</p>
    </div>
  </section>

</body>
</html>
```